Business Card Design

New business card design

Target Market(s)

Residential & Commercial Property Managers

Industry/Entity Type

Plumbing Services

Contact Information for Business Card

Name - Rowan Keddle, title - Director, Phone Number - 0431 286 517, email - rowan@tbk-plumbing.com.au, Company ABN - 73 215 904 386,

Font styles to use
Sans Serif

Colors
0054AA
0677BA
7BADD7
CADEEF
E8F1F8

```html
<!DOCTYPE html>
<html lang="en">
<head>
<meta charset="utf-8">
<title>TBK Plumbing Services – Business Card</title>
<link rel="stylesheet" href="https://fonts.googleapis.com/css2?family=Questrial&family=Roboto:wght@400&display=swap">
<style>
  :root {
    --backdrop: #c4c4c4;
    --card: #1d2229;
    --accent: #00adef;
    --ink: #ffffff;
    --muted-logo: #3e5569;
  }
  * { margin: 0; padding: 0; box-sizing: border-box; }
  html, body {
    width: 1093px; height: 1200px; overflow: hidden;
    background: var(--backdrop);
  }
  .canvas { position: relative; width: 1093px; height: 1200px; }
  .card {
    position: absolute; left: 264px; width: 580px; height: 356px;
    background: var(--card); border-radius: 30px; overflow: hidden;
  }
  .card--front { top: 226px; }
  .card--back { top: 621px; }

  .brand-name {
    font-family: "Roboto", sans-serif; font-weight: 400;
    color: var(--ink); line-height: 1;
  }
  .brand-tagline {
    font-family: "Roboto", sans-serif; font-weight: 400;
    color: var(--ink); text-transform: lowercase; line-height: 1;
  }
  .card--front .brand-name {
    position: absolute; left: 24px; top: 34px; font-size: 54px; letter-spacing: 2px;
  }
  .card--front .brand-tagline {
    position: absolute; left: 36px; top: 109px; font-size: 9px; letter-spacing: 9.6px;
  }

  .name-marker {
    position: absolute; left: -18px; top: 167px; width: 36px; height: 36px;
    border-radius: 50%; background: var(--accent);
  }
  .person-name {
    position: absolute; left: 26px; top: 164px;
    font-family: "Questrial", sans-serif; font-size: 24px; color: var(--ink);
    letter-spacing: 0.5px; line-height: 1;
  }
  .person-title {
    position: absolute; left: 26px; top: 187px;
    font-family: "Roboto", sans-serif; font-size: 17px; color: var(--accent); line-height: 1.2;
  }
  .contact {
    position: absolute; left: 26px; list-style: none;
    font-family: "Roboto", sans-serif; font-size: 17px; color: var(--ink);
  }
  .contact--lines { top: 239px; }
  .contact li { display: flex; align-items: center; gap: 6px; height: 21px; }
  .contact svg { width: 16px; height: 16px; fill: var(--accent); flex: none; }
  .company-abn {
    position: absolute; left: 26px; top: 296px;
    font-family: "Roboto", sans-serif; font-size: 17px; color: var(--ink);
  }
  .feature-disc {
    position: absolute; left: 324px; top: 100px; width: 254px; height: 254px;
    border-radius: 50%; background: var(--accent);
  }

  .back-lockup {
    position: absolute; left: 0; right: 0; top: 112px; text-align: center;
  }
  .card--back .brand-name {
    color: var(--muted-logo); font-size: 74px; letter-spacing: 4px;
  }
  .card--back .brand-tagline {
    color: var(--muted-logo); font-size: 12px; letter-spacing: 15px; margin-top: 24px;
    padding-left: 15px;
  }
</style>
</head>
<body>
<main class="canvas">
  <section class="card card--front" aria-label="Business card front">
    <div class="brand-name">tbk</div>
    <div class="brand-tagline">plumbing services</div>

    <span class="name-marker" aria-hidden="true"></span>
    <h1 class="person-name">Rowan Keddle</h1>
    <p class="person-title">Director</p>

    <ul class="contact contact--lines">
      <li>
        <svg viewBox="0 0 24 24" aria-hidden="true"><path d="M6.6 10.8a15.1 15.1 0 0 0 6.6 6.6l2.2-2.2c.3-.3.7-.4 1-.2 1.1.4 2.3.6 3.6.6.6 0 1 .4 1 1V20c0 .6-.4 1-1 1A17 17 0 0 1 3 4c0-.6.4-1 1-1h3.5c.6 0 1 .4 1 1 0 1.3.2 2.5.6 3.6.1.3 0 .7-.2 1z"/></svg>
        <span>0431 286 517</span>
      </li>
      <li>
        <svg viewBox="0 0 24 24" aria-hidden="true"><path d="M2 5h20v14H2zm2 2v.5l8 5.5 8-5.5V7l-8 5.5z"/></svg>
        <span>rowan@tbk-plumbing.com.au</span>
      </li>
    </ul>
    <p class="company-abn">Company ABN - 73 215 904 386</p>

    <div class="feature-disc" aria-hidden="true"></div>
  </section>

  <section class="card card--back" aria-label="Business card back">
    <div class="back-lockup">
      <div class="brand-name">tbk</div>
      <div class="brand-tagline">plumbing services</div>
    </div>
  </section>
</main>
</body>
</html>
```